Verdant Systems Business Card

want the back of card to be blue- with the logo in the center
front of card- info plus logo (info being mailing address, email address, and website address )
4 different names with titles to have on cards
1) Calvin Borsted - Owner
2) Naomi Trelvik- Customer Relationship Specialist
3) Felix Andrade- Vice President of Sales
4) Owen Markby- Chief Technology Officer

Target Market(s)

tech company in the government/probation office industry

Industry/Entity Type

Government Office

Contact Information for Business Card

1) Calvin Borsted - Owner

Colors
0355a3
ffffff

Requirements
Must have
• back side should be blue, with the logo placed in the center
• front side needs to include both the logo, as well as company info (info should include website address, email address, and mailing address)

```html
<!DOCTYPE html>
<html lang="en">
<head>
<meta charset="utf-8">
<title>Verdant Systems Business Card</title>
<link href="https://fonts.googleapis.com/css2?family=Lora:wght@400;700&display=swap" rel="stylesheet">
<style>
  :root {
    --brand-blue: #0355a3;
    --card-white: #ffffff;
    --text-grey: #7a7a7a;
    --rule-grey: #8a8a8a;
    --stage: #e8e5e0;
    --mark-faint: #f5f6f8;
    --web-soft: #cfe0f3;
  }
  * { margin: 0; padding: 0; box-sizing: border-box; }
  html, body { width: 900px; height: 1200px; overflow: hidden; }
  body {
    position: relative;
    background: var(--stage);
    font-family: "Lora", Georgia, serif;
  }
  .card {
    position: absolute;
    left: 87px;
    width: 735px;
    height: 429px;
    border-radius: 30px;
    box-shadow: 0 6px 14px rgba(0,0,0,0.25);
    overflow: hidden;
  }
  .card--front { top: 137px; background: var(--card-white); }
  .card--back { top: 633px; background: var(--brand-blue); }

  .front__mark {
    position: absolute;
    left: 95px; top: 110px;
    width: 190px; height: 190px;
    border-radius: 50%;
    background: var(--mark-faint);
  }
  .holder {
    position: absolute;
    right: 414px; top: 188px;
    text-align: right;
  }
  .holder__name {
    font-weight: 700;
    font-size: 30px;
    line-height: 1;
    color: var(--brand-blue);
    letter-spacing: 0.3px;
  }
  .holder__title {
    margin-top: 10px;
    font-size: 17px;
    color: var(--text-grey);
    letter-spacing: 0.5px;
  }
  .divider {
    position: absolute;
    left: 353px; top: 150px;
    width: 2px; height: 129px;
    background: var(--rule-grey);
  }
  .contact {
    position: absolute;
    left: 380px; top: 143px;
    font-size: 17.5px;
    color: var(--text-grey);
    line-height: 25px;
  }
  .contact__address { margin-bottom: 10px; }
  .contact__row { display: flex; align-items: center; height: 26.5px; }
  .contact__icon { width: 16px; height: 16px; margin-right: 8px; fill: var(--brand-blue); }
  .accent { color: var(--brand-blue); }

  .back__logo {
    position: absolute;
    left: 0; right: 0; top: 108px;
    display: flex; flex-direction: column; align-items: center;
  }
  .back__dot {
    width: 96px; height: 96px;
    border-radius: 50%;
    background: var(--card-white);
  }
  .back__name {
    margin-top: 26px;
    font-weight: 700;
    font-size: 46px;
    color: var(--card-white);
    line-height: 1;
    letter-spacing: 0.5px;
  }
  .back__web {
    position: absolute;
    left: 0; right: 0; top: 376px;
    text-align: center;
    font-size: 18px;
    color: var(--card-white);
    letter-spacing: 0.3px;
  }
  .back__web .soft { color: var(--web-soft); }
</style>
</head>
<body>
  <section class="card card--front">
    <div class="front__mark" aria-hidden="true"></div>
    <div class="holder">
      <div class="holder__name">CALVIN BORSTED</div>
      <div class="holder__title">Owner</div>
    </div>
    <div class="divider"></div>
    <div class="contact">
      <div class="contact__address">48 Harlow Crescent, Suite A<br>Bristol, UK 400217</div>
      <div class="contact__row">
        <svg class="contact__icon" viewBox="0 0 24 24" aria-hidden="true"><path d="M6.6 10.8a15.1 15.1 0 0 0 6.6 6.6l2.2-2.2a1 1 0 0 1 1-.25 11.4 11.4 0 0 0 3.6.57 1 1 0 0 1 1 1V20a1 1 0 0 1-1 1A17 17 0 0 1 3 4a1 1 0 0 1 1-1h3.5a1 1 0 0 1 1 1c0 1.25.2 2.45.57 3.57a1 1 0 0 1-.25 1z"/></svg>
        <span>000 000 0000</span>
      </div>
      <div class="contact__row">
        <svg class="contact__icon" viewBox="0 0 24 24" aria-hidden="true"><path d="M2 5h20v2l-10 6L2 7z"/><path d="M2 9l10 6 10-6v10H2z"/></svg>
        <span>calvin@<span class="accent">verdantsystems</span>.com</span>
      </div>
      <div class="contact__row">
        <svg class="contact__icon" viewBox="0 0 24 24" aria-hidden="true"><g fill="none" stroke="#0355a3" stroke-width="1.8"><circle cx="12" cy="12" r="9"/><ellipse cx="12" cy="12" rx="4" ry="9"/><path d="M3 12h18M5 7h14M5 17h14"/></g></svg>
        <span>www.<span class="accent">verdantsystems</span>.com</span>
      </div>
    </div>
  </section>

  <section class="card card--back">
    <div class="back__logo">
      <div class="back__dot" aria-hidden="true"></div>
      <div class="back__name">Verdant Systems</div>
    </div>
    <div class="back__web">www.<span class="soft">verdantsystems</span>.com</div>
  </section>
</body>
</html>
```